Summit Ridge Business Card

Side 1: Summit Ridge Logo (logo without Maltese cross) with industrial rope rescue related theme. Our company services - TRAINING - Fire Training, Confined Space Rescue Training, Rope Rescue training, Hazmat Training, Incident Command, EMS, Pump Operations Training. Website - summitridgeexample.com.
Side 2: Summit Ridge Fire Department Logo (logo with Maltese cross) with Firefighter related theme. Company (division) services - FIELD SERVICES - Fire Department, Stand-by Rescue, Safety, EMS, Planning. "Supporting the Emergency Response Community Since 1967"

Add contact information wherever it makes since (Name, Email, Phone).
I would like it to represent the Summit Ridge Fire Department Logo as a division not as a separate entity without saying it, possibly by depicting it in the background of Side 2 instead of being a standalone picture like the logo on Side 1.

```html
<!DOCTYPE html>
<html lang="en">
<head>
<meta charset="utf-8">
<title>Summit Ridge Business Card</title>
<link rel="stylesheet" href="https://fonts.googleapis.com/css2?family=Montserrat:wght@400;500;600;700;800&display=swap">
<style>
  :root {
    --canvas-bg: #2a2a2d;
    --card-black: #0e0e0f;
    --card-edge: #1c1c1e;
    --gloss-dark: #1d1d1f;
    --gloss-mid: #2e2e31;
    --gloss-light: #3a3a3e;
    --brand-red: #e5212b;
    --text-white: #f2f2f2;
    --text-muted: #d6d6d6;
    --text-dim: #8c8c90;
  }
  * { box-sizing: border-box; margin: 0; padding: 0; }
  html, body { width: 1200px; height: 900px; overflow: hidden; }
  body {
    background: var(--canvas-bg);
    font-family: "Montserrat", sans-serif;
    position: relative;
  }
  .card {
    position: absolute;
    left: 250px;
    width: 700px;
    height: 400px;
    border-radius: 22px;
    background: var(--card-black);
    border: 1px solid var(--card-edge);
    overflow: hidden;
  }
  .card--front { top: 30px; }
  .card--back { top: 470px; }

  /* ---------- Front: training side ---------- */
  .front-brand {
    position: absolute;
    left: 0;
    right: 0;
    top: 70px;
    text-align: center;
  }
  .front-brand__name {
    font-weight: 800;
    font-size: 50px;
    letter-spacing: 3px;
    color: var(--gloss-light);
    text-transform: uppercase;
    line-height: 1;
  }
  .front-brand__rule {
    margin: 14px auto 0;
    width: 420px;
    height: 3px;
    background: var(--gloss-mid);
  }
  .training {
    position: absolute;
    left: 60px;
    right: 60px;
    top: 190px;
    text-align: center;
  }
  .training__heading {
    font-weight: 700;
    font-size: 16px;
    letter-spacing: 4px;
    color: var(--brand-red);
    text-transform: uppercase;
  }
  .training__list {
    list-style: none;
    margin-top: 14px;
    display: flex;
    flex-wrap: wrap;
    justify-content: center;
    gap: 8px 22px;
  }
  .training__item {
    font-weight: 500;
    font-size: 13px;
    color: var(--text-dim);
    position: relative;
  }
  .training__item + .training__item::before {
    content: "";
    position: absolute;
    left: -13px;
    top: 7px;
    width: 4px;
    height: 4px;
    border-radius: 50%;
    background: var(--brand-red);
  }
  .front-web {
    position: absolute;
    left: 0;
    right: 0;
    bottom: 34px;
    text-align: center;
    font-weight: 500;
    font-size: 14px;
    letter-spacing: 1px;
    color: var(--text-muted);
  }

  /* ---------- Back: field services side ---------- */
  .division-mark {
    position: absolute;
    right: -90px;
    top: -90px;
    width: 400px;
    height: 400px;
    border-radius: 50%;
    background: radial-gradient(circle at 35% 30%, #262628, var(--gloss-dark) 55%, #131314 100%);
  }
  .division-mark__name {
    position: absolute;
    right: 24px;
    top: 30px;
    width: 300px;
    text-align: right;
    font-weight: 800;
    font-size: 26px;
    line-height: 1.15;
    letter-spacing: 1px;
    color: var(--gloss-light);
    text-transform: uppercase;
  }

  .back-brand {
    position: absolute;
    left: 46px;
    top: 40px;
  }
  .back-brand__name {
    font-weight: 800;
    font-size: 30px;
    letter-spacing: 1px;
    color: var(--brand-red);
    text-transform: uppercase;
    line-height: 1.1;
  }
  .back-brand__rule {
    margin-top: 8px;
    width: 240px;
    height: 3px;
    background: var(--brand-red);
  }

  .person {
    position: absolute;
    left: 70px;
    top: 130px;
  }
  .person__accent {
    position: absolute;
    left: -70px;
    top: 0;
    width: 24px;
    height: 56px;
    background: var(--brand-red);
  }
  .person__name {
    font-weight: 700;
    font-size: 26px;
    color: var(--brand-red);
    line-height: 1.1;
  }
  .person__title {
    font-weight: 500;
    font-size: 15px;
    color: var(--text-white);
    margin-top: 4px;
  }

  .contact {
    position: absolute;
    left: 70px;
    top: 220px;
    list-style: none;
  }
  .contact__item {
    display: flex;
    align-items: flex-start;
    gap: 12px;
    font-size: 14px;
    color: var(--text-muted);
    line-height: 1.3;
    margin-bottom: 7px;
  }
  .contact__icon {
    width: 15px;
    height: 15px;
    flex: none;
    margin-top: 2px;
    fill: var(--brand-red);
  }

  .field-services {
    position: absolute;
    left: 440px;
    top: 150px;
    width: 230px;
  }
  .field-services__heading {
    font-weight: 700;
    font-size: 15px;
    letter-spacing: 3px;
    color: var(--brand-red);
    text-transform: uppercase;
  }
  .field-services__list {
    list-style: none;
    margin-top: 10px;
  }
  .field-services__item {
    font-weight: 500;
    font-size: 14px;
    color: var(--text-white);
    line-height: 1.6;
    padding-left: 14px;
    position: relative;
  }
  .field-services__item::before {
    content: "";
    position: absolute;
    left: 0;
    top: 9px;
    width: 5px;
    height: 5px;
    background: var(--brand-red);
  }
  .tagline {
    position: absolute;
    left: 440px;
    right: 24px;
    bottom: 26px;
    font-weight: 600;
    font-size: 12px;
    line-height: 1.4;
    color: var(--text-dim);
  }
</style>
</head>
<body>
  <section class="card card--front" aria-label="Business card front, training">
    <div class="front-brand">
      <div class="front-brand__name">Summit Ridge</div>
      <div class="front-brand__rule"></div>
    </div>

    <div class="training">
      <div class="training__heading">Training</div>
      <ul class="training__list">
        <li class="training__item">Fire Training</li>
        <li class="training__item">Confined Space Rescue</li>
        <li class="training__item">Rope Rescue</li>
        <li class="training__item">Hazmat</li>
        <li class="training__item">Incident Command</li>
        <li class="training__item">EMS</li>
        <li class="training__item">Pump Operations</li>
      </ul>
    </div>

    <div class="front-web">www.summitridgeexample.com</div>
  </section>

  <section class="card card--back" aria-label="Business card back, field services">
    <div class="division-mark" aria-hidden="true"></div>
    <div class="division-mark__name">Summit Ridge<br>Fire Department</div>

    <div class="back-brand">
      <div class="back-brand__name">Summit Ridge</div>
      <div class="back-brand__rule"></div>
    </div>

    <div class="person">
      <div class="person__accent"></div>
      <div class="person__name">Daniel Hartwell</div>
      <div class="person__title">Managing Director</div>
    </div>

    <ul class="contact">
      <li class="contact__item">
        <svg class="contact__icon" viewBox="0 0 16 16" aria-hidden="true"><path d="M8 0a5.5 5.5 0 0 0-5.5 5.5C2.5 10 8 16 8 16s5.5-6 5.5-10.5A5.5 5.5 0 0 0 8 0zm0 7.7a2.2 2.2 0 1 1 0-4.4 2.2 2.2 0 0 1 0 4.4z"/></svg>
        <span>418 Harbor View Rd, #112<br>Millbrook, OH 43000</span>
      </li>
      <li class="contact__item">
        <svg class="contact__icon" viewBox="0 0 16 16" aria-hidden="true"><path d="M3.6 1l2.3 3.1-1.4 1.6a9 9 0 0 0 5.8 5.8l1.6-1.4L15 12.4l-1.6 2.4C7 15 1 9 1.2 2.6z"/></svg>
        <span>877-555-0142</span>
      </li>
      <li class="contact__item">
        <svg class="contact__icon" viewBox="0 0 16 16" aria-hidden="true"><path d="M1 3h14v10H1zm1.4 1.2L8 8.6l5.6-4.4z"/></svg>
        <span>info@summitridgeexample.com</span>
      </li>
      <li class="contact__item">
        <svg class="contact__icon" viewBox="0 0 16 16" aria-hidden="true"><circle cx="8" cy="8" r="7"/></svg>
        <span>www.summitridgeexample.com</span>
      </li>
    </ul>

    <div class="field-services">
      <div class="field-services__heading">Field Services</div>
      <ul class="field-services__list">
        <li class="field-services__item">Fire Department</li>
        <li class="field-services__item">Stand-by Rescue</li>
        <li class="field-services__item">Safety</li>
        <li class="field-services__item">EMS</li>
        <li class="field-services__item">Planning</li>
      </ul>
    </div>

    <p class="tagline">Supporting the Emergency Response Community Since 1967</p>
  </section>
</body>
</html>
```